Resident Guide for Senior Living Community

I need to create an informational magazine for residents that live in an Assisted Living community. This magazine is designed to educate the resident about the different service options and features that the community provides. I don't want to use any of the pictures in the Word Document - please use the uploaded picture instead. The final design should be both informational and elegant. The text in the word document is the actual text that needs to be used in the Resident Guide. Thanks!

Target Market(s)

Senior citizens and adult children (55 - 65 years old)

Industry/Entity Type

Assisted Living

Requirements
Must have
• Must be elegant - think Velmont Hargrove. Needs to have a lot of pictures and the logo must be used. The logo is the Plaque that says The Birch Lodge.
Nice to have
• The Word doucment is the old Resident Guide - we are looking for a refresh using the same content.
Should not have
• please do not use any pictures from the Word Document other than the Logo.

```html
<!DOCTYPE html>
<html lang="en">
<head>
<meta charset="utf-8">
<title>The Birch Lodge – Resident Guide Spread</title>
<link href="https://fonts.googleapis.com/css2?family=Lato:wght@300;400;700;900&display=swap" rel="stylesheet">
<style>
  :root {
    --bg: #ececec;
    --paper: #ffffff;
    --gold: #b39634;
    --gold-text: #bba24e;
    --gold-dark: #a1842a;
    --ink-dark: #3a3a3a;
  }
  * { box-sizing: border-box; margin: 0; padding: 0; }
  html, body { width: 1200px; height: 1000px; overflow: hidden; }
  body { background: var(--bg); font-family: "Lato", sans-serif; position: relative; }

  .spread { position: absolute; left: 184px; top: 165px; width: 848px; height: 600px; background: var(--paper); overflow: hidden; }
  .page { position: absolute; top: 0; width: 424px; height: 600px; }
  .page--left { left: 0; }
  .page--right { left: 424px; }

  .running-head { position: absolute; top: 14px; font-size: 7px; font-weight: 300; color: var(--gold-text); white-space: nowrap; }
  .running-head strong { font-weight: 700; color: var(--gold-dark); }
  .page--left .running-head { left: 26px; }
  .page--right .running-head { right: 27px; }
  .head-rule { position: absolute; top: 25px; height: 2px; background: var(--gold); }
  .page--left .head-rule { left: 26px; width: 368px; }
  .page--right .head-rule { left: 28px; width: 369px; }

  .reason { position: absolute; font-size: 8.6px; line-height: 12.9px; font-weight: 300; color: var(--gold-text); text-align: justify; }
  .page--left .reason { left: 26px; width: 368px; }
  .page--right .reason { left: 28px; width: 369px; }
  .reason b { font-weight: 900; font-size: 11.5px; color: var(--gold-dark); }

  .photo { position: absolute; }
  .photo--plate-a { left: 26px; top: 288px; width: 128px; height: 89px; background: radial-gradient(ellipse at 50% 70%, #e9e3da 0 28%, #7a4b2e 40%, #1c1410 75%); }
  .photo--plate-b { left: 160px; top: 288px; width: 97px; height: 89px; background: radial-gradient(circle at 50% 50%, #f6f2ea 0 34%, #d8b98a 60%, #c9a371 100%); }
  .photo--plate-c { left: 263px; top: 288px; width: 131px; height: 89px; background: radial-gradient(ellipse at 55% 72%, #efe9df 0 26%, #8a5a3c 42%, #171210 78%); }
  .photo--suite { left: 29px; top: 379px; width: 368px; height: 221px; background: linear-gradient(180deg, #efe9df 0%, #e6dccc 45%, #f3f1ee 75%, #dcd6cc 100%); }

  .tagline { position: absolute; left: 26px; top: 514px; width: 368px; text-align: center; color: var(--gold-dark); }
  .tagline__title { font-size: 12.5px; font-weight: 900; line-height: 14.5px; }
  .tagline__sub { font-size: 10.5px; font-weight: 400; line-height: 14.5px; margin-top: 0; }
</style>
</head>
<body>
  <main class="spread">
    <section class="page page--left">
      <p class="running-head">18 Reasons Why <strong>The Birch Lodge</strong> Is Most Preferred By Prospects And Families With High Expectations.</p>
      <div class="head-rule"></div>

      <p class="reason" style="top:40px"><b>9.</b> The Birch Lodge is routinely able to manage very frail and/or challenging health (Alzheimer's/ advanced memory issues) of persons other Assisted Living or Nursing Homes reject/refuse because of their less favorable staffing ratios (meaning less time being spent with each resident) and their inability to provide the hands on care your loved one requires and you desire.</p>

      <p class="reason" style="top:117px"><b>10.</b> Very competitive, all inclusive rates, include all hospitality, health and intensive 24/7 personal care services. One guaranteed price, based on our assessment and your service choices, with no surprises at the end of the month.</p>

      <p class="reason" style="top:168px"><b>11.</b> Our operating philosophy from Day One has been to provide the level of care needed by each resident each hour of the day, which can fluctuate and change without notice. Our delivered services are not fixed at a specific care-for-cost level. We do not contract for a single, inflexible, restrictive care level; where we would possibly need to change it frequently (adding ala-carte costs for a higher care level). We are finding that a good number of residents move to The Birch Lodge from outside facilities simply because they weren't receiving the care they were paying for. We adjust to our resident's needs daily-he/she doesn't have to adjust to our schedule!</p>

      <div class="photo photo--plate-a" role="img" aria-label="Plated entrée with garnish on a white dinner plate, glassware behind"></div>
      <div class="photo photo--plate-b" role="img" aria-label="Top view of a fish dish with asparagus on a white plate"></div>
      <div class="photo photo--plate-c" role="img" aria-label="Plated sandwich course with flowers and glassware on a dining table"></div>

      <p class="reason" style="top:380px"><b>12.</b> Finest menus prepared by our own top chefs. All special diets honored. For years, we have set the standard for fine food service in Assisted Living since our founding in 1988. From scratch cooking and baking using the freshest meats, fish and produce.</p>

      <p class="reason" style="top:431px"><b>13.</b> We can assist with difficult end-of-life decisions and facilitate healthcare choices by our residents and their family. Our company owns two (2) Medicare and Medicaid certified Hospice in-patient units (IPU's), operated by Stillwater in Sandy Springs and Meadowlight Hospice in Cumming. The Birch Lodges are adjacent to both Hospice IPU's. mes to enable them to remain independent or semi-independent for as long as possible.</p>

      <div class="tagline">
        <p class="tagline__title">We Are Not Just<br>A Licensed Assisted Living Home, But Rather</p>
        <p class="tagline__sub">The Finest Combination Of Quality Hospitality And Assisted<br>Living Healthcare Services Available.</p>
      </div>
    </section>

    <section class="page page--right">
      <p class="running-head">18 Reasons Why <strong>The Birch Lodge</strong> Is Most Preferred By Prospects And Families With High Expectations.</p>
      <div class="head-rule"></div>

      <p class="reason" style="top:38px"><b>14.</b> As of July 2017, we will have launched BirchCare Home Health, operating out of both of our Birch Lodges in Sandy Springs and Cumming on a Private pay basis (no Medicare/Medicaid billing on our part). This represents a commitment to return to In Home Care where we owned and operated a major program 10 years ago. We have many requests for our staff to do private duty for residents. We now are extending that to the homes of our neighbors in Sandy Springs and metro Atlanta as well as Cumming, Forsyth Co., Cobb Co., Cherokee Co., etc., to make our solid and exceptional area services</p>

      <p class="reason" style="top:141px"><b>15.</b> Stimulating, dignified, entertaining, and mentally stimulating social, exercise programs, based on the capabilities and functionality of each resident. Our Activity Directors coordinates outings, exercise, stimulating entertainment, games and special events.</p>

      <p class="reason" style="top:206px"><b>16.</b> Personal laundry and linens washed and hand ironed at no extra charge.</p>

      <p class="reason" style="top:232px"><b>17.</b> Residents' accommodations are all private suites and penthouse apartments. Central heating and air conditioning with individual thermostats in each suite for your own personal preference. The Birch Lodge is secured and sprinkled, with all safety and emergency systems.</p>

      <p class="reason" style="top:296px"><b>18.</b> We have the most professional, experienced, stable licensed assisted living management and staff of any care home in Atlanta and Cumming. Our annual turnover is less than 10%. Most Assisted Living properties average anywhere between 50% to 100%. We have two (2) employees who have been with us over 28 years, the majority over 8 years!</p>

      <div class="photo photo--suite" role="img" aria-label="Bright private resident suite with a made bed, dresser, lamps and closet doors"></div>
    </section>
  </main>
</body>
</html>
```